Business Cards

Need business card design that I can update for new employees and details. Needs to incorporate our logo, be bright and fun (in line with tourism and holidays)
Would like a Map of Western Australia on the front with locations all the caravan parks we own (just purchased Tom Price so please include that as well as others listed on our website).
Target Market(s)
Famillies
Contact Information for Business Card
5 Cards -
Neil Perrow (Director) e: perrow@wattlebay.com.au p: 0491 570 156
Mira Perrow (Director) e: perrow@wattlebay.com.au p: 0491 570 157
Owen Halvey (General Manager) e: halvey@wattlebay.com.au p: 0491 570 158
Helen Halvey (General Manager) e: halvey@wattlebay.com.au p: 0491 570 159
Colin Danby (Training and Operations Manager) - e: danby@wattlebay.com.au p:0491 570 110
Colors
Look and feel

```html
<!DOCTYPE html>
<html lang="en">
<head>
<meta charset="utf-8">
<title>Wattle Bay Tourist Parks — Business Card</title>
<link rel="stylesheet" href="https://fonts.googleapis.com/css2?family=Marcellus&family=Open+Sans:wght@400&display=swap">
<style>
  :root {
    --page: #f1f1f0;
    --teal: #40c0cb;
    --sea-green: #66bfb0;
    --white: #ffffff;
    --card-grey: #e6e6e6;
    --ink-grey: #5c5c5c;
    --serif: "Marcellus", "Times New Roman", serif;
    --sans: "Open Sans", Arial, sans-serif;
  }
  html, body {
    margin: 0;
    width: 1200px;
    height: 900px;
    overflow: hidden;
    background: var(--page);
  }
  .canvas {
    position: relative;
    width: 1200px;
    height: 900px;
  }
  .card {
    position: absolute;
    box-shadow: 0 2px 8px rgba(0,0,0,0.12);
    overflow: hidden;
  }

  /* Front of card */
  .card-front {
    left: 78px;
    top: 34px;
    width: 588px;
    height: 364px;
    background: var(--teal);
  }
  .card-front .wave {
    position: absolute;
    left: 0;
    top: 0;
  }
  .card-front .brand {
    position: absolute;
    right: 36px;
    top: 72px;
    margin: 0;
    font-family: var(--serif);
    font-weight: 400;
    font-size: 20px;
    letter-spacing: 3px;
    text-transform: uppercase;
    color: var(--white);
    text-align: right;
  }
  .contact {
    position: absolute;
    right: 36px;
    top: 170px;
    text-align: right;
    color: var(--white);
  }
  .contact .person-name {
    margin: 0;
    font-family: var(--serif);
    font-weight: 400;
    font-size: 25px;
    line-height: 30px;
    text-transform: uppercase;
  }
  .contact .person-role {
    margin: 2px 0 0;
    font-family: var(--sans);
    font-size: 15px;
    line-height: 20px;
  }
  .contact .details {
    list-style: none;
    margin: 22px 0 0;
    padding: 0;
    font-family: var(--sans);
    font-size: 15px;
    line-height: 22px;
  }
  .contact .details li {
    display: flex;
    justify-content: flex-end;
    align-items: center;
    gap: 4px;
  }
  .contact .icon {
    width: 13px;
    height: 13px;
    fill: var(--white);
  }

  /* Back of card */
  .card-back {
    left: 388px;
    top: 505px;
    width: 566px;
    height: 352px;
    background: var(--card-grey);
    display: flex;
    flex-direction: column;
    align-items: center;
    justify-content: center;
    gap: 22px;
  }
  .card-back .brand-square {
    width: 84px;
    height: 84px;
    background: var(--teal);
  }
  .card-back .brand {
    margin: 0;
    font-family: var(--serif);
    font-weight: 400;
    font-size: 26px;
    letter-spacing: 4px;
    text-transform: uppercase;
    color: var(--ink-grey);
  }
</style>
</head>
<body>
<main class="canvas">

  <section class="card card-front" aria-label="Business card front">
    <svg class="wave" width="588" height="364" viewBox="0 0 588 364" aria-hidden="true">
      <path d="M0 222 C110 210 210 232 290 290 C325 314 350 320 400 320 L588 320 L588 364 L0 364 Z" fill="var(--white)"/>
      <path d="M0 240 C110 230 205 252 280 305 C315 330 345 336 400 336 L588 336 L588 364 L0 364 Z" fill="var(--sea-green)"/>
    </svg>

    <p class="brand">Wattle Bay Tourist Parks</p>

    <div class="contact">
      <p class="person-name">Neil Perrow</p>
      <p class="person-role">Director</p>
      <ul class="details">
        <li>0491 570 156
          <svg class="icon" viewBox="0 0 24 24" aria-label="phone"><path d="M6.6 10.8c1.4 2.8 3.8 5.1 6.6 6.6l2.2-2.2c.3-.3.7-.4 1-.2 1.1.4 2.3.6 3.6.6.6 0 1 .4 1 1V20c0 .6-.4 1-1 1C10.6 21 3 13.4 3 4c0-.6.4-1 1-1h3.5c.6 0 1 .4 1 1 0 1.3.2 2.5.6 3.6.1.3 0 .7-.2 1z"/></svg>
        </li>
        <li>perrow@wattlebay.com.au
          <svg class="icon" viewBox="0 0 24 24" aria-label="email"><path d="M2 5h20v14H2z M3.5 6.5v.4l8.5 6 8.5-6v-.4z" fill-rule="evenodd"/></svg>
        </li>
      </ul>
    </div>
  </section>

  <section class="card card-back" aria-label="Business card back">
    <div class="brand-square" aria-hidden="true"></div>
    <p class="brand">Wattle Bay Tourist Parks</p>
  </section>

</main>
</body>
</html>
```